Fenwick Ridge Accounting - New client package

I need a stationary package (presentation folder cover, welcome letter template/design, sample financial report template/design, business card and new logo) for my accounting business. I would like to see designs that use the color blue. Financial icons can be included in the design. The final design should be clean and communicate professionalism and the use of modern; user-friendly technology. Attached postcard files should help with overall design concept.

```html
<!DOCTYPE html>
<html lang="en">
<head>
<meta charset="utf-8">
<title>Fenwick Ridge Accounting – Business Card</title>
<link href="https://fonts.googleapis.com/css2?family=Roboto:wght@400;500;700&family=Oswald:wght@500&display=swap" rel="stylesheet">
<style>
  :root {
    --stage: #181818;
    --card: #f8f9f9;
    --blue: #2e5d8c;
    --blue-bright: #336699;
    --slate: #3d4244;
    --ink: #3a3a3a;
  }
  * { margin: 0; padding: 0; box-sizing: border-box; }
  html, body { width: 1200px; height: 1200px; overflow: hidden; }
  body { background: var(--stage); font-family: "Roboto", sans-serif; color: var(--ink); position: relative; }

  .card { position: absolute; left: 318px; width: 562px; height: 339px; background: var(--card); overflow: hidden; }
  .card--front { top: 251px; }
  .card--back { top: 609px; }

  .brand-dot { position: absolute; border-radius: 50%; background: var(--blue); }
  .wordmark { position: absolute; color: var(--blue); font-family: "Roboto", sans-serif; font-weight: 700; line-height: 1; white-space: nowrap; }
  .wordmark__name { display: block; letter-spacing: 0.5px; }
  .wordmark__sub { display: block; }

  .card--front .brand-dot { left: 226px; top: 65px; width: 112px; height: 112px; }
  .card--front .wordmark { left: 0; width: 562px; top: 189px; text-align: center; }
  .card--front .wordmark__name { font-size: 36px; }
  .card--front .wordmark__sub { font-size: 17px; letter-spacing: 12px; margin-top: 8px; padding-left: 12px; }

  .front-url { position: absolute; left: 0; width: 562px; top: 295px; text-align: center; font-size: 14px; color: var(--ink); }
  .front-url__rule { display: inline-block; width: 38px; height: 3px; vertical-align: middle; margin: 0 14px; background: linear-gradient(90deg, transparent, var(--blue) 30%, var(--blue) 70%, transparent); }

  .front-bar { position: absolute; left: 0; bottom: 0; width: 562px; height: 14px; display: flex; }
  .front-bar__blue { flex: 1; background: var(--blue-bright); }
  .front-bar__slate { flex: 1; background: var(--slate); }

  .card--back .brand-dot { left: 26px; top: 53px; width: 94px; height: 94px; }
  .card--back .wordmark { left: 148px; top: 78px; }
  .card--back .wordmark__name { font-size: 36px; }
  .card--back .wordmark__sub { font-size: 17px; letter-spacing: 12px; margin-top: 8px; padding-left: 4px; }

  .holder { position: absolute; left: 26px; top: 188px; }
  .holder__name { font-family: "Oswald", sans-serif; font-weight: 500; font-size: 23px; color: var(--blue-bright); line-height: 1; }
  .holder__role { font-size: 14px; margin-top: 7px; }
  .address { position: absolute; left: 26px; top: 264px; font-size: 14px; line-height: 21px; }

  .contacts { position: absolute; left: 300px; top: 207px; list-style: none; font-size: 14px; }
  .contacts li { display: flex; align-items: center; height: 21.5px; }
  .contacts svg { width: 13px; height: 13px; margin-right: 13px; fill: var(--blue-bright); }

  .back-bands { position: absolute; left: 0; top: 0; }
  .tagline { position: absolute; left: 296px; top: 309px; font-size: 14.5px; color: #fff; letter-spacing: 0.2px; }
</style>
</head>
<body>

<section class="card card--front" aria-label="Business card front">
  <span class="brand-dot"></span>
  <div class="wordmark">
    <span class="wordmark__name">FENWICK RIDGE</span>
    <span class="wordmark__sub">ACCOUNTING</span>
  </div>
  <p class="front-url"><span class="front-url__rule"></span>www.fenwickridgeaccounting.com<span class="front-url__rule"></span></p>
  <div class="front-bar"><span class="front-bar__blue"></span><span class="front-bar__slate"></span></div>
</section>

<section class="card card--back" aria-label="Business card back">
  <svg class="back-bands" width="562" height="339" viewBox="0 0 562 339" aria-hidden="true">
    <rect x="0" y="325" width="240" height="14" fill="var(--slate)"/>
    <path d="M226 339 L248 306 Q254 297 266 297 L562 297 L562 339 Z" fill="var(--blue-bright)"/>
  </svg>

  <span class="brand-dot"></span>
  <div class="wordmark">
    <span class="wordmark__name">FENWICK RIDGE</span>
    <span class="wordmark__sub">ACCOUNTING</span>
  </div>

  <div class="holder">
    <p class="holder__name">Dana Whitlow</p>
    <p class="holder__role">Managing Director</p>
  </div>
  <p class="address">58 Harbor Lane, Millbrook,<br>Stonefield, US 204718</p>

  <ul class="contacts">
    <li><svg viewBox="0 0 16 16" aria-hidden="true"><path d="M1 6 Q8 1 15 6 L13 8 L11 6 L5 6 L3 8 Z"/><path d="M4 8 L12 8 L14 14 L2 14 Z"/></svg>1.877.555.0142</li>
    <li><svg viewBox="0 0 16 16" aria-hidden="true"><path d="M1 3 H15 V13 H1 Z M2.5 4.5 L8 9 L13.5 4.5 V11.5 L10 8 L8 10 L6 8 L2.5 11.5 Z" fill-rule="evenodd"/></svg>info@fenwickridgeaccounting.com</li>
    <li><svg viewBox="0 0 16 16" aria-hidden="true"><path d="M8 1 A7 7 0 1 0 8.01 1 Z M2.6 7 H5 Q5.1 4 6.3 2.4 Q3.2 3.5 2.6 7 Z M6 7 H10 Q9.9 3.8 8 2.2 Q6.1 3.8 6 7 Z M11 7 H13.4 Q12.8 3.5 9.7 2.4 Q10.9 4 11 7 Z M2.6 9 Q3.2 12.5 6.3 13.6 Q5.1 12 5 9 Z M6 9 Q6.1 12.2 8 13.8 Q9.9 12.2 10 9 Z M11 9 Q10.9 12 9.7 13.6 Q12.8 12.5 13.4 9 Z" fill-rule="evenodd"/></svg>www.fenwickridgeaccounting.com</li>
  </ul>

  <p class="tagline">BOUTIQUE ACCOUNTING FIRM</p>
</section>

</body>
</html>
```